Building technology company seek stationery design and folder design

Letterhead, and a folder design
ideally, I would have two letter head design, one is for one-page bussiness letter. the other one I can use for longer document such report, or analysis regular report page
you can find company logo and overall style at our website:
www.structavolt.example

we are in building technology business, using internet of things technology to improve building energy efficiency to make building greener.

Industry/Entity Type

It Company

Requirements
Must have
• company logo
Nice to have
• techy look abstract graphics, etc.
Should not have
• no comment

```html
<!DOCTYPE html>
<html lang="en">
<head>
<meta charset="utf-8">
<title>Structavolt Stationery</title>
<link href="https://fonts.googleapis.com/css2?family=Questrial&display=swap" rel="stylesheet">
<style>
  :root {
    --backdrop: #e0e0e0;
    --paper: #ffffff;
    --paper-shade: #f1f1f1;
    --brand-green: #8dc63f;
    --folder-lime: #bfdc6c;
    --folder-pale: #f7faf0;
    --ink: #5f5f55;
    --ink-soft: #7a7a70;
    --band-grey: #6e6a58;
    --net-grey: #d6d6d6;
    --net-blue: #cfe7ee;
    --white: #ffffff;
  }
  * { margin: 0; padding: 0; box-sizing: border-box; }
  html, body {
    width: 1200px; height: 821px; overflow: hidden;
    background: var(--backdrop);
    font-family: "Questrial", "Century Gothic", sans-serif;
  }
  .canvas { position: relative; width: 1200px; height: 821px; }

  /* Letterhead */
  .letterhead {
    position: absolute; left: 74px; top: 114px; width: 441px; height: 620px;
    background: linear-gradient(90deg, var(--paper) 0%, var(--paper) 35%, var(--paper-shade) 100%);
    box-shadow: 0 1px 3px rgba(0,0,0,0.18);
    overflow: hidden;
  }
  .letterhead__skyline {
    position: absolute; left: 0; top: 366px; width: 441px; height: 212px;
    background: linear-gradient(180deg, rgba(214,214,214,0) 0%, rgba(214,214,214,0.55) 100%);
  }
  .letterhead__brand {
    position: absolute; left: 0; top: 78px; width: 441px; text-align: center;
    font-size: 17px; letter-spacing: 2px; color: var(--brand-green);
  }
  .letterhead__salutation {
    position: absolute; left: 40px; top: 174px;
    font-size: 11px; color: var(--ink);
  }
  .letterhead__body {
    position: absolute; left: 40px; top: 207px; width: 366px;
    font-size: 6px; line-height: 9.5px; color: var(--ink-soft);
  }
  .letterhead__body p { margin-bottom: 9.5px; }
  .letterhead__closing {
    position: absolute; left: 40px; top: 406px;
    font-size: 6px; color: var(--ink-soft);
  }
  .letterhead__signature {
    position: absolute; left: 36px; top: 432px; width: 80px; height: 30px;
    background: linear-gradient(90deg, rgba(141,198,63,0.35), rgba(141,198,63,0.1));
    border-radius: 3px;
  }
  .letterhead__footer {
    position: absolute; left: 0; top: 578px; width: 441px; height: 24px;
    display: flex;
  }
  .footer__contacts {
    flex: 0 0 406px; background: var(--brand-green);
    display: flex; align-items: center; gap: 6px;
    padding-left: 51px; font-size: 6px; color: var(--white);
  }
  .footer__item { display: flex; align-items: center; gap: 2px; }
  .footer__item svg { width: 6px; height: 6px; }
  .footer__name {
    margin-left: auto; margin-right: 8px; font-size: 8px; letter-spacing: 1px;
  }
  .footer__tail { flex: 1; background: var(--band-grey); }

  /* Folder */
  .folder {
    position: absolute; left: 553px; top: 77px; width: 520px; height: 658px;
    background: linear-gradient(180deg, var(--folder-lime) 0%, #d4e89c 40%, #eaf4d4 70%, var(--folder-pale) 100%);
    box-shadow: 0 1px 3px rgba(0,0,0,0.18);
    overflow: hidden;
  }
  .folder__brand {
    position: absolute; left: 0; top: 150px; width: 520px; text-align: center;
    font-size: 30px; letter-spacing: 4px; color: var(--white);
  }
  .folder__skyline {
    position: absolute; left: 0; top: 355px; width: 520px; height: 303px;
    background: linear-gradient(180deg, rgba(207,231,238,0) 0%, rgba(207,231,238,0.7) 100%);
  }
</style>
</head>
<body>
<main class="canvas">

  <section class="letterhead" aria-label="Letterhead">
    <div class="letterhead__skyline" role="img" aria-label="Faint network-line city skyline illustration"></div>
    <div class="letterhead__brand">STRUCTAVOLT</div>

    <p class="letterhead__salutation">Dear Mr. Hale,</p>

    <div class="letterhead__body">
      <p>Thank you for meeting with our team last week. We have reviewed the energy data from your three office buildings and prepared a short summary of the savings our connected sensors can deliver across lighting, heating and cooling systems. Each sensor reports every minute, so your facility staff can see usage in real time and act before waste grows into cost.</p>
      <p>During the pilot phase we will install gateways on each floor and link them to our cloud platform. Your team will receive a dashboard login, weekly reports and a direct line to our support engineers. Most clients see results within the first two months of operation, with the largest gains in lighting schedules and air handling.</p>
      <p>The attached proposal covers hardware, installation, training and a full year of monitoring. Prices are fixed for ninety days from the date of this letter. If your board approves the plan this quarter, we can begin work on the first building next month and complete all three sites before the summer cooling season starts. We would also welcome a visit from your engineers to our test lab.</p>
      <p>Please review the proposal at your convenience and let us know a good time to talk. We look forward to helping you make your buildings greener, quieter and less costly to run.</p>
    </div>

    <p class="letterhead__closing">Sincerely,</p>
    <div class="letterhead__signature" role="img" aria-label="Handwritten signature of Daniel Hale"></div>

    <footer class="letterhead__footer">
      <div class="footer__contacts">
        <span class="footer__item">
          <svg viewBox="0 0 10 10"><path d="M2 1 L4 1 L5 3 L4 4 Q5 6 6 6 L7 5 L9 6 L9 8 Q8 9 7 9 Q1 8 1 2 Q1 1 2 1Z" fill="#fff"/></svg>
          (555) 010-0142
        </span>
        <span class="footer__item">
          <svg viewBox="0 0 10 10"><rect x="1" y="2" width="8" height="6" fill="#fff"/><path d="M1 2 L5 5 L9 2" stroke="#8dc63f" fill="none"/></svg>
          info@structavolt.example
        </span>
        <span class="footer__item">
          <svg viewBox="0 0 10 10"><circle cx="5" cy="5" r="4" fill="#fff"/></svg>
          www.structavolt.example
        </span>
        <span class="footer__item">structavolt</span>
        <span class="footer__name">STRUCTAVOLT</span>
      </div>
      <div class="footer__tail"></div>
    </footer>
  </section>

  <section class="folder" aria-label="Presentation folder">
    <div class="folder__skyline" role="img" aria-label="Light blue network-line city skyline illustration"></div>
    <div class="folder__brand">STRUCTAVOLT</div>
  </section>

</main>
</body>
</html>
```